Wholesale in Gold Jewellery & Gold Bullion

We are an established gold jewellery and gold bullion wholesaler selling these products to international clients. We already have a name and logo of our company, hence please view attached current card design. We need a completely new design to compliment our business and industry and the final design should be new and elegant.

Contact Information for Business Card

New card details must be same as per current card. Like logo, name, tel no. & etc.

Colors

Designer to choose colors to be used in the design.

```html
<!DOCTYPE html>
<html lang="en">
<head>
<meta charset="utf-8">
<title>Ravelle &amp; Co – Business Card</title>
<link href="https://fonts.googleapis.com/css2?family=Bebas+Neue&family=Lato:wght@400&display=swap" rel="stylesheet">
<style>
  :root {
    --backdrop: #353535;
    --card-white: #f4f4f4;
    --gold: #d9960f;
    --ink: #1f1f1f;
    --white: #ffffff;
  }
  * { margin: 0; padding: 0; box-sizing: border-box; }
  html, body { width: 1200px; height: 900px; overflow: hidden; }
  body { background: var(--backdrop); position: relative; font-family: "Lato", sans-serif; }

  .card { position: absolute; top: 200px; width: 310px; height: 502px; }
  .card-front {
    left: 253px; background: var(--card-white);
    border-radius: 62px 0 62px 0;
  }
  .card-back {
    left: 627px; background: var(--gold);
    border-radius: 0 62px 0 62px;
  }

  .brand-dot {
    position: absolute; left: 96px; top: 96px;
    width: 104px; height: 104px; border-radius: 50%;
    background: var(--gold);
  }
  .brand-name {
    position: absolute; left: 32px; top: 196px; width: 240px;
    font-family: "Bebas Neue", sans-serif; font-size: 58px; line-height: 1;
    color: var(--gold); white-space: nowrap;
  }

  .contact { position: absolute; left: 33px; top: 310px; color: var(--ink); font-size: 14px; line-height: 18px; }
  .person-name {
    font-family: "Bebas Neue", sans-serif; font-size: 21px; line-height: 20px;
    color: var(--gold); letter-spacing: 0.3px;
  }
  .person-role { margin-bottom: 6px; }
  .address { margin-bottom: 8px; }
  .contact-list { list-style: none; }
  .contact-list li { display: flex; align-items: center; gap: 5px; }
  .contact-list svg { width: 12px; height: 12px; fill: var(--gold); flex: none; }

  .back-name {
    position: absolute; left: 0; right: 0; top: 222px; text-align: center;
    font-family: "Bebas Neue", sans-serif; font-size: 58px; line-height: 1;
    color: var(--white);
  }
</style>
</head>
<body>
  <section class="card card-front">
    <div class="brand-dot"></div>
    <div class="brand-name">Ravelle &amp; Co</div>

    <div class="contact">
      <div class="person-name">Arun Mehtani</div>
      <div class="person-role">Director</div>
      <div class="address">12 Marlow Lane,<br>Singapore 208411</div>
      <ul class="contact-list">
        <li>
          <svg viewBox="0 0 12 12" aria-hidden="true"><path d="M1 4.5C1 3 3 2 6 2s5 1 5 2.5V5H8.5V4H3.5v1H1zM2.5 6h7l1 4.5h-9zM6 7a1.3 1.3 0 1 0 0 2.6A1.3 1.3 0 0 0 6 7z"/></svg>
          +65 6410 2250
        </li>
        <li>
          <svg viewBox="0 0 12 12" aria-hidden="true"><path d="M3.5 0.5h5a1 1 0 0 1 1 1v9a1 1 0 0 1-1 1h-5a1 1 0 0 1-1-1v-9a1 1 0 0 1 1-1zM4 2v7h4V2zM6 9.6a.6.6 0 1 0 0 1.2.6.6 0 0 0 0-1.2z"/></svg>
          +65 9183 4426
        </li>
        <li>
          <svg viewBox="0 0 12 12" aria-hidden="true"><path d="M3 1h6v3H3zM1 4.5h10v4.5H9.5V7.5h-7V9H1zM3 8h6v3H3z"/></svg>
          +65 6372 5518
        </li>
        <li>
          <svg viewBox="0 0 12 12" aria-hidden="true"><path d="M1 2.5h10v7H1zM1.8 3.2 6 6.4l4.2-3.2v-.1H1.8z"/></svg>
          arun@ravelleco.com
        </li>
      </ul>
    </div>
  </section>

  <section class="card card-back">
    <div class="back-name">Ravelle &amp; Co</div>
  </section>
</body>
</html>
```